Automotive Accessories Business Card

Design a business template that match our new logo design and our industry.

https://www.qelmotorgear.com/

Target Market(s)

Aftermarket auto parts and accessories

Industry/Entity Type

automotive

Contact Information for Business Card

company logo

Font styles to use
Serif
Sans Serif

Colors
EB3D1F
EC4F4E
F09395
F8D3D4
FCEDEE

```html
<!DOCTYPE html>
<html lang="en">
<head>
<meta charset="utf-8">
<title>QEL Motor Gear – Business Card</title>
<link href="https://fonts.googleapis.com/css2?family=Arimo:wght@400;700&display=swap" rel="stylesheet">
<style>
  :root {
    --stage-bg: #c9c9c9;
    --card-white: #ffffff;
    --card-dark: #2a2a2a;
    --brand-red: #d91f26;
    --ink: #1e1e1e;
    --ink-soft: #3c3c3c;
    --mark-grey: #8a8a8a;
    --rule: #1e1e1e;
  }
  * { box-sizing: border-box; margin: 0; padding: 0; }
  html, body { width: 1200px; height: 800px; overflow: hidden; }
  body {
    background: var(--stage-bg);
    font-family: "Arimo", Arial, sans-serif;
    position: relative;
  }
  .card {
    position: absolute;
    top: 250px;
    width: 520px;
    height: 298px;
    border-bottom: 3px solid var(--brand-red);
    box-shadow: 0 10px 24px rgba(0,0,0,0.18);
  }
  .card--front { left: 50px; background: var(--card-white); }
  .card--back  { left: 630px; background: var(--card-dark); }

  /* Front */
  .front__brand {
    position: absolute;
    right: 48px;
    top: 52px;
    display: flex;
    align-items: center;
    gap: 10px;
    font-weight: 700;
    font-size: 26px;
    letter-spacing: 1px;
    color: var(--ink-soft);
    text-transform: uppercase;
  }
  .brand-square { width: 18px; height: 18px; background: var(--brand-red); }
  .front__person { position: absolute; left: 34px; top: 118px; }
  .person__name {
    color: var(--brand-red);
    font-weight: 700;
    font-size: 19px;
    letter-spacing: 0.3px;
    text-transform: uppercase;
  }
  .person__title { color: var(--ink); font-size: 16px; margin-top: 2px; }
  .front__rule {
    position: absolute;
    left: 34px; right: 30px; top: 168px;
    height: 1px; background: var(--rule);
  }
  .front__contacts {
    position: absolute; left: 34px; top: 182px;
    list-style: none;
    font-size: 15px; color: var(--ink);
    line-height: 25px;
  }
  .front__contacts li { display: flex; align-items: center; gap: 9px; }
  .front__contacts svg { width: 14px; height: 14px; flex: none; }
  .accent { color: var(--brand-red); }
  .front__address {
    position: absolute; right: 30px; top: 182px;
    text-align: right; font-size: 15px; color: var(--ink);
    line-height: 22px;
  }

  /* Back */
  .back__brand {
    position: absolute; inset: 0;
    display: flex; align-items: center; justify-content: center; gap: 12px;
    font-weight: 700; font-size: 32px; letter-spacing: 1.5px;
    color: var(--mark-grey); text-transform: uppercase;
  }
  .back__brand .brand-square { background: var(--mark-grey); width: 22px; height: 22px; }
</style>
</head>
<body>
  <section class="card card--front" aria-label="Business card front">
    <div class="front__brand"><span class="brand-square"></span>QEL Motor Gear Inc</div>

    <div class="front__person">
      <p class="person__name">Daniel Brooks</p>
      <p class="person__title">Managing Director</p>
    </div>

    <div class="front__rule"></div>

    <ul class="front__contacts">
      <li>
        <svg viewBox="0 0 16 16" aria-hidden="true"><path fill="var(--brand-red)" d="M3.5 1.5l2.5 0 1 3.5-1.6 1.2a8 8 0 0 0 4.4 4.4L11 9l3.5 1v2.5c0 1-1 2-2 2C6.5 14.5 1.5 9.5 1.5 3.5c0-1 1-2 2-2z"/></svg>
        044-123 456 789
      </li>
      <li>
        <svg viewBox="0 0 16 16" aria-hidden="true"><rect x="1" y="3" width="14" height="10" fill="var(--brand-red)"/><path d="M1.5 3.5L8 9l6.5-5.5" stroke="#fff" stroke-width="1.4" fill="none"/></svg>
        info@qelmotorgear.com
      </li>
      <li>
        <svg viewBox="0 0 16 16" aria-hidden="true"><circle cx="8" cy="8" r="7" fill="var(--brand-red)"/><g stroke="#fff" stroke-width="1" fill="none"><ellipse cx="8" cy="8" rx="3" ry="7"/><path d="M1 8h14M2.5 4.5h11M2.5 11.5h11"/></g></svg>
        <span>www.<span class="accent">qelmotorgear</span>.com</span>
      </li>
    </ul>

    <address class="front__address" style="font-style:normal">
      421 , Address line goes here<br>45452,Country Name
    </address>
  </section>

  <section class="card card--back" aria-label="Business card back">
    <div class="back__brand"><span class="brand-square"></span>QEL Motor Gear Inc</div>
  </section>
</body>
</html>
```